R7M Horizon Business Card Design

We need a business card created for our New Business "R7M Horizon"<br/><br/>The business card design is up to you however the following information must be on the business card:<br/><br/>Front of the business card -<br/>Email :darrenp@r7mhorizon.nz<br/>Mobile: +64 (0) 22 4870 619<br/>Website: www.r7mhorizon.nz<br/>Card Owner Name: Darren Paltrow<br/>Company Title: Business Development Manager<br/>Slogan: "The BEST of both worlds". <br/>Logo On the front attached to the design brief<br/><br/>On the back: <br/>Space on the back for 4 more versions of the logo across the bottom of the card indicating different subsidiary brands - R7M Coffee, R7M Arts, R7M ?? (The card will be used for all of these brands - We Will add the extra subsidiary logos to the design once the design is finished (We are a graphics design team). <br/><br/>Other than that we want a premium feeling logo that remains universally usable depending on the business entity that we are using the card for. The use of bright bold colours would be great but we still want the card to feel premium.
Target Market(s)
Gift Design and Manufacturing Companies
Contact Information for Business Card
Front of the business card -
Email :darrenp@r7mhorizon.nz
Mobile: +64 (0) 22 4870 619
Website: www.r7mhorizon.nz
Card Owner Name: Darren Paltrow
Company Title: Business Development Manager
Slogan: "The BEST of both worlds".
Logo On the front attached to the design brief

```html
<!DOCTYPE html>
<html lang="en">
<head>
<meta charset="utf-8">
<title>R7M Horizon Business Card</title>
<link href="https://fonts.googleapis.com/css2?family=Source+Sans+3:wght@400;600;700&display=swap" rel="stylesheet">
<style>
  :root {
    --brand-blue: #34479b;
    --ink: #2b2b2b;
    --paper: #ffffff;
    --backdrop: #d6d6d6;
  }
  * { box-sizing: border-box; margin: 0; padding: 0; }
  html, body {
    width: 1200px; height: 900px; overflow: hidden;
    background: var(--backdrop);
    font-family: "Source Sans 3", Arial, sans-serif;
  }
  .canvas {
    width: 1200px; height: 900px;
    display: flex; flex-direction: column; align-items: center; justify-content: center;
    gap: 50px;
  }
  .card {
    position: relative;
    width: 630px; height: 360px;
    box-shadow: 0 6px 18px rgba(0,0,0,0.18);
  }

  /* Back of card */
  .card-back { background: var(--brand-blue); color: var(--paper); }
  .brand-mark {
    position: absolute; display: flex; align-items: center; gap: 18px;
  }
  .brand-mark .dot {
    border: 6px solid currentColor; border-radius: 50%;
  }
  .card-back .brand-mark { left: 150px; top: 100px; }
  .card-back .brand-mark .dot { width: 92px; height: 92px; }
  .card-back .brand-name { font-size: 56px; font-weight: 700; letter-spacing: 1px; }

  .subsidiaries {
    position: absolute; left: 40px; right: 40px; bottom: 36px;
    display: flex; justify-content: space-between;
  }
  .subsidiary { display: flex; align-items: center; gap: 8px; }
  .subsidiary .dot {
    width: 30px; height: 30px; border: 3px solid var(--paper); border-radius: 50%;
  }
  .subsidiary .label { font-size: 19px; font-weight: 700; }

  /* Front of card */
  .card-front { background: var(--paper); color: var(--ink); }
  .card-front .brand-mark { right: 40px; top: 34px; color: var(--brand-blue); gap: 12px; }
  .card-front .brand-mark .dot { width: 52px; height: 52px; border-width: 4px; }
  .card-front .brand-name { font-size: 32px; font-weight: 700; }
  .rule { position: absolute; height: 1px; background: var(--brand-blue); }
  .rule-top { left: 330px; right: 40px; top: 112px; }
  .slogan {
    position: absolute; right: 40px; top: 136px;
    color: var(--brand-blue); font-size: 18px;
  }
  .person { position: absolute; left: 40px; top: 214px; }
  .person-name {
    color: var(--brand-blue); font-size: 21px; font-weight: 700;
    text-transform: uppercase; letter-spacing: 0.3px;
  }
  .person-title { font-size: 15px; margin-top: 1px; }
  .rule-mid { left: 40px; width: 300px; top: 272px; }
  .contacts { position: absolute; left: 40px; top: 282px; list-style: none; }
  .contacts li {
    display: flex; align-items: center; gap: 8px;
    font-size: 14px; line-height: 21px;
  }
  .contacts svg { width: 13px; height: 13px; flex: none; }
</style>
</head>
<body>
<main class="canvas">

  <section class="card card-back" aria-label="Business card back">
    <div class="brand-mark">
      <span class="dot"></span>
      <span class="brand-name">R7M Horizon</span>
    </div>
    <div class="subsidiaries">
      <div class="subsidiary"><span class="dot"></span><span class="label">R7M Coffee</span></div>
      <div class="subsidiary"><span class="dot"></span><span class="label">R7M Arts</span></div>
      <div class="subsidiary"><span class="dot"></span><span class="label">R7M Coffee</span></div>
      <div class="subsidiary"><span class="dot"></span><span class="label">R7M Arts</span></div>
    </div>
  </section>

  <section class="card card-front" aria-label="Business card front">
    <div class="brand-mark">
      <span class="dot"></span>
      <span class="brand-name">R7M Horizon</span>
    </div>
    <div class="rule rule-top"></div>
    <p class="slogan">The BEST of both worlds</p>

    <div class="person">
      <p class="person-name">Darren Paltrow</p>
      <p class="person-title">Business Development Manager</p>
    </div>
    <div class="rule rule-mid"></div>

    <ul class="contacts">
      <li>
        <svg viewBox="0 0 13 13" aria-hidden="true"><rect x="3" y="0.5" width="7" height="12" rx="1.2" fill="none" stroke="#34479b" stroke-width="1.2"/><line x1="5.5" y1="10.5" x2="7.5" y2="10.5" stroke="#34479b"/></svg>
        <span>+64 (0) 22 4870 619</span>
      </li>
      <li>
        <svg viewBox="0 0 13 13" aria-hidden="true"><rect x="0.6" y="2.5" width="11.8" height="8" fill="none" stroke="#34479b" stroke-width="1.2"/><polyline points="0.6,2.5 6.5,7.5 12.4,2.5" fill="none" stroke="#34479b" stroke-width="1.2"/></svg>
        <span>darrenp@r7mhorizon.nz</span>
      </li>
      <li>
        <svg viewBox="0 0 13 13" aria-hidden="true"><circle cx="6.5" cy="6.5" r="5.8" fill="none" stroke="#34479b" stroke-width="1.2"/><ellipse cx="6.5" cy="6.5" rx="2.4" ry="5.8" fill="none" stroke="#34479b"/><line x1="0.7" y1="6.5" x2="12.3" y2="6.5" stroke="#34479b"/></svg>
        <span>www.r7mhorizon.nz</span>
      </li>
    </ul>
  </section>

</main>
</body>
</html>
```